Business card for law firm

Need business card for new law firm. Think confident, authoritative, conservative, but not stuffy or old-fashioned.

Contact Information for Business Card

Content for card - logo (uploaded), plus the following:

Paul Whitcombe (larger font)
Managing Partner (larger font, but not as large as name)
Level 9, 7 Ferris Lane
Sydney NSW 2000
Main Tel 02 9364 2710
Direct Tel 02 8472 3159
Email paul@qvlegal.com.au
www.qvlegal.com.au

Letterhead design should include logo plus:
Level 9, 7 Ferris Lane
Sydney NSW 2000
Tel 02 8472 3159
www.qvlegal.com.au

```html
<!DOCTYPE html>
<html lang="en">
<head>
<meta charset="utf-8">
<title>Quayvale Legal — Business Card</title>
<link rel="stylesheet" href="https://fonts.googleapis.com/css2?family=Open+Sans:wght@400;600;700&display=swap">
<style>
  :root {
    --stage: #202022;
    --card-white: #ffffff;
    --navy: #0f1f5c;
    --ink: #0b0b0c;
    --text-dark: #141414;
    --text-light: #ffffff;
    --text-muted: #3a3a3a;
  }
  * { box-sizing: border-box; margin: 0; padding: 0; }
  html, body {
    width: 1200px; height: 960px; overflow: hidden;
    background: var(--stage);
    font-family: "Open Sans", sans-serif;
  }
  .stage {
    width: 1200px; height: 960px;
    display: flex; flex-direction: column; align-items: center; justify-content: center;
    gap: 44px;
  }
  .card {
    position: relative;
    width: 700px; height: 400px;
    background: var(--card-white);
    overflow: hidden;
    box-shadow: 0 10px 30px rgba(0,0,0,0.35);
  }

  /* Wordmark: plain name with one square */
  .wordmark {
    display: flex; align-items: center;
    font-family: "Open Sans", sans-serif; font-weight: 600;
    color: var(--text-dark); white-space: nowrap;
  }
  .wordmark__square { background: var(--navy); flex: none; }

  /* Front face */
  .front__wordmark {
    position: absolute; left: 60px; top: 140px;
    gap: 26px; font-size: 46px;
  }
  .front__wordmark .wordmark__square { width: 92px; height: 92px; }
  .front__web {
    position: absolute; left: 178px; top: 262px;
    font-size: 15px; letter-spacing: 3px; color: var(--text-muted);
  }

  /* Back face */
  .back__shape { position: absolute; inset: 0; }
  .back__wordmark {
    position: absolute; left: 36px; top: 142px;
    gap: 12px; font-size: 27px;
  }
  .back__wordmark .wordmark__square { width: 36px; height: 36px; }
  .back__title {
    position: absolute; right: 28px; top: 46px;
    text-align: right; color: var(--text-light);
    text-transform: uppercase;
  }
  .title__name { font-weight: 700; font-size: 23px; letter-spacing: 0.5px; line-height: 1.2; }
  .title__role { font-weight: 400; font-size: 16px; letter-spacing: 0.5px; }
  .back__contact {
    position: absolute; left: 420px; top: 140px;
    font-size: 16px; line-height: 1.6;
    color: var(--text-light); list-style: none;
  }
  .contact__line { display: flex; align-items: center; gap: 7px; }
  .contact__line--plain { padding-left: 21px; }
  .contact__icon { width: 14px; height: 14px; flex: none; }
</style>
</head>
<body>
<main class="stage">

  <section class="card card--front" aria-label="Card front">
    <div class="wordmark front__wordmark">
      <span class="wordmark__square"></span>
      <span class="wordmark__name">Quayvale Legal</span>
    </div>
    <div class="front__web">www.qvlegal.com.au</div>
  </section>

  <section class="card card--back" aria-label="Card back">
    <svg class="back__shape" width="700" height="400" viewBox="0 0 700 400">
      <polygon points="470,0 700,0 700,400 200,400" fill="var(--ink)"/>
      <polygon points="380,40 700,40 700,118 420,118 400,84" fill="var(--navy)"/>
    </svg>

    <div class="wordmark back__wordmark">
      <span class="wordmark__square"></span>
      <span class="wordmark__name">Quayvale Legal</span>
    </div>

    <div class="back__title">
      <div class="title__name">Paul Whitcombe</div>
      <div class="title__role">Managing Partner</div>
    </div>

    <ul class="back__contact">
      <li class="contact__line contact__line--plain">Level 9, 7 Ferris Lane</li>
      <li class="contact__line contact__line--plain">Sydney NSW 2000</li>
      <li class="contact__line">
        <svg class="contact__icon" viewBox="0 0 16 16"><circle cx="8" cy="8" r="7" fill="none" stroke="#fff" stroke-width="1.4"/><path d="M5.5 4.5l1.5 1.8-1 1c.6 1.2 1.4 2 2.6 2.6l1-1 1.8 1.5-1 1.2C8 11.4 4.8 8.2 4.6 5.4z" fill="#fff"/></svg>
        02 9364 2710(Main)
      </li>
      <li class="contact__line">
        <svg class="contact__icon" viewBox="0 0 16 16"><circle cx="8" cy="8" r="7" fill="none" stroke="#fff" stroke-width="1.4"/><path d="M5.5 4.5l1.5 1.8-1 1c.6 1.2 1.4 2 2.6 2.6l1-1 1.8 1.5-1 1.2C8 11.4 4.8 8.2 4.6 5.4z" fill="#fff"/></svg>
        02 8472 3159(Direct)
      </li>
      <li class="contact__line">
        <svg class="contact__icon" viewBox="0 0 16 16"><rect x="1.5" y="3.5" width="13" height="9" fill="none" stroke="#fff" stroke-width="1.4"/><path d="M1.5 3.5l6.5 5 6.5-5" fill="none" stroke="#fff" stroke-width="1.4"/></svg>
        paul@qvlegal.com.au
      </li>
      <li class="contact__line">
        <svg class="contact__icon" viewBox="0 0 16 16"><circle cx="8" cy="8" r="6.5" fill="none" stroke="#fff" stroke-width="1.3"/><ellipse cx="8" cy="8" rx="2.8" ry="6.5" fill="none" stroke="#fff" stroke-width="1.1"/><path d="M1.5 8h13" stroke="#fff" stroke-width="1.1"/></svg>
        www.qvlegal.com.au
      </li>
    </ul>
  </section>

</main>
</body>
</html>
```